Brand new letterhead, business card, email signature etc.

We are a financial company in London, UK. Our website is www.marlowvane.com. We're wanting a complete remodel of the company colours, letter head, business cards, email signatures, etc. Looking to keep the same font for the company name. I have upload a colour palette that we want to work with. We're looking for company letterhead for outgoing letters/ correspondence, letterhead for internal documentation, email signatures, e-letters. etc. Ultimately we will redesign the entire website also. It is important that our clients get a strong, secure, warm, trustworthy, solid feeling and first impression.
Updates

Designs look the same

Target Market(s)

Institutional investors, (ultra) high net worth individuals

Industry/Entity Type

Finance, Invesments banking.

Font styles to use
Other font styles liked:
• Current font is "Champagne & Limousines"

Requirements
Must have
• Must use the colours provided on the PDF uploaded to the portal. The purple = main colour. The red = accent colour.
Nice to have
• Nice to use same font as now for the company name "Corvane". Font is "Champagne & Limousines". Nice to have some reference to the old logo flower, but only subtle.
Should not have
• Do not use the colour red from our website. Use the colours provided on the colour palette PDF that I uploaded in the portal.

```html
<!DOCTYPE html>
<html lang="en">
<head>
<meta charset="utf-8">
<title>Corvane Stationery Set</title>
<link rel="stylesheet" href="https://fonts.googleapis.com/css2?family=Josefin+Sans:wght@300;400;600&display=swap">
<style>
:root{
  --plum:#26001a;
  --accent:#c0231b;
  --paper:#f4f4f2;
  --ground:#e4e4e6;
  --ink:#3a3a3a;
  --muted:#6b6b6b;
}
*{box-sizing:border-box;margin:0;padding:0}
html,body{width:1200px;height:792px;overflow:hidden;background:var(--ground);font-family:"Josefin Sans",sans-serif;color:var(--ink)}
.canvas{position:relative;width:1200px;height:792px}
.sheet{position:absolute;background:var(--paper);overflow:hidden}

/* brand lockup */
.brand{position:absolute;display:flex;align-items:center;white-space:nowrap}
.brand-mark{border:1px solid var(--plum);flex:none}
.brand-name{font-family:"Josefin Sans",sans-serif;font-weight:300;color:var(--plum);text-transform:uppercase}

/* business card back */
.card-back{left:184px;top:132px;width:170px;height:97px}
.card-back .band{position:absolute;left:0;width:100%;height:29px;background:var(--plum)}
.card-back .band.top{top:0}.card-back .band.bottom{bottom:0}
.card-back .brand{left:24px;top:36px;gap:8px}
.card-back .brand-mark{width:24px;height:24px}
.card-back .brand-name{font-size:13px;letter-spacing:3.4px}

/* business card front */
.card-front{left:379px;top:132px;width:169px;height:97px}
.frame{position:absolute;border:1.5px solid var(--plum)}
.card-front .frame{inset:7px}
.card-front .brand{left:43px;top:25px;gap:5px}
.card-front .brand-mark{width:18px;height:18px}
.card-front .brand-name{font-size:9px;letter-spacing:2.6px}
.contact-strip{position:absolute;color:var(--accent);text-align:center}
.contact-strip .row{border-top:.6px solid var(--plum);display:flex;justify-content:center}
.contact-strip .row:last-child{border-bottom:.6px solid var(--plum)}
.contact-strip .row span{flex:1}
.contact-strip .row span+span{border-left:.6px solid var(--plum)}
.card-front .contact-strip{left:35px;top:64px;width:99px;font-size:3.6px}
.card-front .contact-strip .row{padding:2px 0}

/* compliment slip */
.slip{left:184px;top:255px;width:365px;height:182px}
.slip .frame{inset:13px 14px 14px 14px}
.slip .brand{left:118px;top:43px;gap:8px}
.slip .brand-mark{width:32px;height:28px}
.slip .brand-name{font-size:17px;letter-spacing:5px}
.slip .contact-strip{left:117px;top:132px;width:131px;font-size:5px}
.slip .contact-strip .row{padding:3px 0}

/* envelope */
.envelope{left:184px;top:468px;width:365px;height:182px}
.envelope .flap{position:absolute;left:0;top:0;width:365px;height:47px}
.envelope .brand{left:104px;top:82px;gap:9px}
.envelope .brand-mark{width:38px;height:33px}
.envelope .brand-name{font-size:19px;letter-spacing:5.4px}

/* letterhead */
.letterhead{left:595px;top:131px;width:367px;height:519px}
.letterhead .edge{position:absolute;inset:0;width:367px;height:519px}
.letterhead .brand{left:40px;top:42px;gap:9px}
.letterhead .brand-mark{width:38px;height:33px}
.letterhead .brand-name{font-size:20px;letter-spacing:5.6px}
.sender{position:absolute;left:40px;top:134px}
.person-name{font-weight:600;font-size:7.6px;color:var(--plum);letter-spacing:.3px}
.person-role{font-size:4.6px;letter-spacing:1.6px;color:var(--muted);text-transform:uppercase;margin-top:1px}
.sender-details{margin-top:6px;font-size:4.6px;line-height:7.4px;color:#222}
.sender-details b{font-weight:400;color:var(--accent)}
.letter-date{position:absolute;right:44px;top:176px;font-size:5.4px;color:#222}
.letter-date b{font-weight:400;color:var(--accent)}
.letter-body{position:absolute;left:40px;top:208px;width:287px;font-size:6.6px;line-height:8.1px;text-align:justify;font-weight:300;color:#333}
.letter-body p+p{margin-top:8px}
.signature{position:absolute;left:262px;top:360px;width:63px;height:22px;background:linear-gradient(90deg,rgba(38,0,26,.08),rgba(38,0,26,.18));border-radius:2px}
.signatory{position:absolute;right:42px;top:385px;text-align:right}
.signatory .person-role{letter-spacing:1.9px}
.letter-footer{position:absolute;left:50px;top:454px;width:280px;display:flex;justify-content:space-between;font-size:5px;line-height:6.6px;color:#222}
.footer-item{display:flex;align-items:center;gap:11px}
.footer-item svg{width:10px;height:10px;flex:none}
</style>
</head>
<body>
<main class="canvas">

  <section class="sheet card-back" aria-label="Business card, back">
    <div class="band top"></div>
    <div class="brand"><span class="brand-mark"></span><span class="brand-name">Corvane</span></div>
    <div class="band bottom"></div>
  </section>

  <section class="sheet card-front" aria-label="Business card, front">
    <div class="frame"></div>
    <div class="brand"><span class="brand-mark"></span><span class="brand-name">Corvane</span></div>
    <div class="contact-strip">
      <div class="row"><span>14 Aldgate Row, London EC3N 2QT, UK.</span></div>
      <div class="row"><span>www.marlowvane.com</span><span>info@marlowvane.com</span></div>
    </div>
  </section>

  <section class="sheet slip" aria-label="Compliment slip">
    <div class="frame"></div>
    <div class="brand"><span class="brand-mark"></span><span class="brand-name">Corvane</span></div>
    <div class="contact-strip">
      <div class="row"><span>14 Aldgate Row, London EC3N 2QT, UK.</span></div>
      <div class="row"><span>www.marlowvane.com</span><span>info@marlowvane.com</span></div>
    </div>
  </section>

  <section class="sheet envelope" aria-label="Envelope">
    <svg class="flap" viewBox="0 0 365 47" aria-hidden="true">
      <path d="M0 0H365L361 30Q359 46 343 46H22Q6 46 4 30Z" fill="var(--plum)"/>
    </svg>
    <div class="brand"><span class="brand-mark"></span><span class="brand-name">Corvane</span></div>
  </section>

  <section class="sheet letterhead" aria-label="Letterhead">
    <svg class="edge" viewBox="0 0 727 1027" preserveAspectRatio="none" aria-hidden="true">
      <polygon points="437,0 727,0 727,291 695,271 695,32 463,32" fill="var(--plum)"/>
      <polygon points="0,515 32,543 32,992 542,992 574,1027 0,1027" fill="var(--plum)"/>
      <g stroke-width="3">
        <line x1="558" y1="102" x2="695" y2="102" stroke="var(--plum)"/>
        <line x1="586" y1="110" x2="695" y2="110" stroke="var(--accent)"/>
        <line x1="616" y1="117" x2="695" y2="117" stroke="var(--plum)"/>
      </g>
      <circle cx="558" cy="102" r="5" fill="var(--plum)"/>
      <circle cx="586" cy="110" r="3.5" fill="var(--accent)"/>
      <circle cx="616" cy="117" r="3" fill="var(--plum)"/>
    </svg>

    <div class="brand"><span class="brand-mark"></span><span class="brand-name">Corvane</span></div>

    <div class="sender">
      <div class="person-name">ELENA R. WHITCOMBE</div>
      <div class="person-role">Marketing Manager</div>
      <div class="sender-details">
        <div><b>PHONE :</b> +44 20 7946 0381</div>
        <div><b>WEB :</b> www.marlowvane.com</div>
        <div><b>ADDR :</b> 48 FENCHURCH LANE</div>
        <div>LONDON EC3M 4AJ</div>
      </div>
    </div>
    <div class="letter-date"><b>DATE :</b> 26-July-2015</div>

    <div class="letter-body">
      <p>Lorem ipsum dolor sit amet, consectetur adipiscing elit, sed do eiusmod tempor incididunt ut labore et dolore magna aliqua. Quis ipsum suspendisse ultrices gravida. Risus commodo viverra maecenas accumsan lacus vel facilisis. Lorem ipsum dolor sit amet, consectetur adipiscing elit, sed do eiusmod tempor incididunt ut labore et dolore magna aliqua. Quis ipsum suspendisse ultrices gravida.</p>
      <p>Lorem ipsum dolor sit amet, consectetur adipiscing elit, sed do eiusmod tempor incididunt ut labore et dolore magna aliqua. Quis ipsum suspendisse ultrices gravida. Risus commodo viverra maecenas accumsan lacus vel facilisis. Lorem ipsum dolor sit amet, consectetur adipiscing elit, sed do eiusmod tempor incididunt ut labore et dolore magna aliqua. Quis ipsum suspendisse ultrices gravida. Risus commodo viverra maecenas accumsan lacus vel facilisis.</p>
      <p>Lorem ipsum dolor sit amet, consectetur adipiscing elit, sed do eiusmod tempor incididunt ut labore et dolore magna aliqua. Quis ipsum suspendisse ultrices gravida. Risus commodo viverra maecenas accumsan lacus vel facilisis. Lorem ipsum dolor sit amet, consectetur adipiscing elit, sed do eiusmod tempor incididunt ut labore et dolore magna aliqua. Quis ipsum suspendisse ultrices gravida. Risus commodo viverra maecenas accumsan lacus vel facilisis.</p>
    </div>

    <div class="signature" role="img" aria-label="Handwritten signature of the signatory"></div>
    <div class="signatory">
      <div class="person-name">SAMUEL T. ASHDOWN</div>
      <div class="person-role">Creative Designer</div>
    </div>

    <footer class="letter-footer">
      <div class="footer-item">
        <svg viewBox="0 0 24 24" aria-hidden="true"><path fill="var(--accent)" d="M6.6 10.8a15.2 15.2 0 0 0 6.6 6.6l2.2-2.2c.3-.3.7-.4 1-.2 1.1.4 2.3.6 3.6.6.6 0 1 .4 1 1V20c0 .6-.4 1-1 1A17 17 0 0 1 3 4c0-.6.4-1 1-1h3.5c.6 0 1 .4 1 1 0 1.3.2 2.5.6 3.6.1.3 0 .7-.2 1z"/></svg>
        <div>+44 20 7946 0527<br>+44 20 7946 0527</div>
      </div>
      <div class="footer-item">
        <svg viewBox="0 0 24 24" aria-hidden="true"><g fill="none" stroke="var(--accent)" stroke-width="2"><circle cx="12" cy="12" r="9"/><path d="M3 12h18M12 3c3 3 3 15 0 18M12 3c-3 3-3 15 0 18"/></g></svg>
        <div>www.marlowvane.com<br>office@marlowvane.com</div>
      </div>
      <div class="footer-item">
        <svg viewBox="0 0 24 24" aria-hidden="true"><path fill="var(--accent)" d="M12 2a7 7 0 0 0-7 7c0 5 7 13 7 13s7-8 7-13a7 7 0 0 0-7-7zm0 9.5A2.5 2.5 0 1 1 12 6.5a2.5 2.5 0 0 1 0 5z"/></svg>
        <div>9 Cornhill Court<br>London EC3V 3ND</div>
      </div>
    </footer>
  </section>

</main>
</body>
</html>
```